Venture Capital firm needs modern business cards

We are a Venture Capital firm within financial services/Asset management. The industry generally has basic business cards with black, blue and maybe green/yellow design elements.
Our firm has a four-colour swoosh logo. We are based in London and want to stand out, just a little bit!, from the crowd. Our company is called LORV Investments and the 'C' stands for collaboration thus using makerswarm is a natural portal for our business card design competition. Our logo came via makerswarm too!
We use 'Venture Partner in Asset Management' as our tagline and this is Trademark registered. We operate in a conservative industry and we should not overstep our mark. The logo is colorful as it is and therefore the rest of the design should not be too fanciful.
The objective is twofold: make our logo element stick and memorable with our audience, whilst representing a conservative yet young image.
Updates
The Business Card obviously needs a field for Name, Surname, Job Title, Adress fields: Street, City, Postcode, Country, telefone and cell number, website address, etc.
We have uploaded the ai file. We trust that these are OK. If not, please advise.
Reason: We have have been busy with a client engagement. We will set the project as Guaranteed in return for the troubles we cause. Apologies for the confusion.
Thank you all for these great and creative design suggestions. The team is very happy with a number of your ideas! We will be in touch tomorrow to give individual feedback before the project closes on Friday. We look forward to working with some of you to narrow down your creations. Thank you, LORV Investments team.
All,
Target Market(s)
Financial Services Professionals, Investors, Media, 35-70 years, mainly male, well educated
Industry/Entity Type
Conservative
Requirements
Must have
- We must make use of our logo and potential tagline 'Venture Partner in Asset Management' as we are establishing a new Brand and new company in the market.
We can use 'LORV', 'LORV Investments', and 'LORV Investments'+tagline 'Venture Partner in Asset Management' or simply the four-colour swoosh plus the name of the company as part of the text. (see files)
All design elements are available in black or grey-scale if required. (grey scale swoosh attached).
Due to regulation we must have the following wording on the card in small print 'LORV Investments is an Appointed Representative of Bramwell Holdings Partnership Limited, which is authorised by the Monetary Oversight Board'.
Nice to have
- We would consider designs that make use of different printing techniques such embossing/debossing, UV spot etc.
We attach our colour palette in the files section for your reference.
Should not have
- The font we use for our company name is 'EXO' so do not use a font style that clashes with the corporate fonts, please.
Do not use other design elements than the ones we provide in the file library as part of this project.

```html
<!DOCTYPE html>
<html lang="en">
<head>
<meta charset="utf-8">
<title>LORV Investments – Business Cards</title>
<link rel="stylesheet" href="https://fonts.googleapis.com/css2?family=Exo:wght@400;500&display=swap">
<style>
  :root {
    --stage: #2c2c2c;
    --card: #ffffff;
    --pattern-tint: #efefef;
    --ink: #3a3a3a;
    --ink-soft: #6a6a6a;
    --plum: #6b1d52;
    --mark: #3a3a3a;
  }
  * { box-sizing: border-box; margin: 0; padding: 0; }
  html, body {
    width: 1200px; height: 900px; overflow: hidden;
    background: var(--stage);
    font-family: "Exo", "Helvetica Neue", Arial, sans-serif;
  }
  .canvas { position: relative; width: 1200px; height: 900px; }
  .card {
    position: absolute; top: 288px;
    width: 520px; height: 325px;
    background: var(--card);
    box-shadow: 0 14px 30px rgba(0,0,0,.45);
  }
  .card--front { left: 50px; }
  .card--back { left: 630px; }

  .front-pattern {
    position: absolute; inset: 0;
    background: linear-gradient(135deg, #f4f4f4, var(--pattern-tint));
  }
  .front-brand {
    position: absolute; left: 150px; top: 118px;
    display: flex; align-items: center; gap: 14px;
  }
  .brand-dot {
    width: 40px; height: 40px; border-radius: 50%;
    background: var(--mark);
  }
  .brand-name {
    font-weight: 500; color: var(--mark);
    font-size: 58px; line-height: 1; letter-spacing: 1px;
  }
  .front-tagline {
    position: absolute; left: 204px; top: 186px;
    font-size: 10px; color: var(--ink-soft); letter-spacing: .3px;
  }

  .back-brand {
    position: absolute; left: 32px; top: 40px;
    display: flex; align-items: center; gap: 12px;
  }
  .back-brand .brand-dot { width: 32px; height: 32px; }
  .back-brand .brand-name { font-size: 46px; }
  .back-brand-sub {
    position: absolute; left: 76px; top: 94px;
    font-size: 11px; letter-spacing: 3px; color: var(--ink-soft);
  }
  .contact {
    position: absolute; right: 30px; top: 108px;
    width: 300px; color: var(--ink);
  }
  .contact-name { font-size: 21px; color: var(--plum); font-weight: 500; }
  .contact-role { font-size: 13px; color: var(--ink-soft); margin-bottom: 18px; }
  .contact-line { font-size: 12px; line-height: 17px; }
  .contact-line .label { color: var(--plum); display: inline-block; width: 12px; }
  .contact-address { margin-top: 14px; font-size: 12px; line-height: 17px; }
  .contact-web { font-size: 12px; color: var(--plum); }
  .disclaimer {
    position: absolute; left: 32px; bottom: 22px; width: 420px;
    font-size: 8px; line-height: 11px; color: var(--ink-soft);
  }
</style>
</head>
<body>
<main class="canvas">
  <section class="card card--front" aria-label="Business card front">
    <div class="front-pattern" role="img" aria-label="Faint repeating brand pattern across the card face"></div>
    <div class="front-brand">
      <span class="brand-dot"></span>
      <span class="brand-name">LORV</span>
    </div>
    <p class="front-tagline">Venture Partner in Asset Management</p>
  </section>

  <section class="card card--back" aria-label="Business card back">
    <div class="back-brand">
      <span class="brand-dot"></span>
      <span class="brand-name">LORV</span>
    </div>
    <p class="back-brand-sub">investments</p>

    <div class="contact">
      <p class="contact-name">Tobias Wrenfield</p>
      <p class="contact-role">managing director</p>
      <p class="contact-line"><span class="label">m</span> 07700 XXX XXX</p>
      <p class="contact-line"><span class="label">e</span> tobias.wrenfield@lorvinvestments.com</p>
      <p class="contact-address">Harrow Court | 18 Elmstead Row<br>London | EC4N 7QT | United Kingdom</p>
      <p class="contact-web">www.lorvinvestments.com</p>
    </div>

    <p class="disclaimer">LORV Investments is an Appointed Representative of Bramwell Holdings Partnership Limited, which is authorised and regulated by the Monetary Oversight Board</p>
  </section>
</main>
</body>
</html>
```